Harlow Creek Church Invite Card

We are a vibrant multigenerational church outside of Raleigh, NC and are wanting a 'church invite card' that we can encourage our members to carry with them so that they can invite their friends to church.

These cards should have a modern feel (see http://brightmosaic.com/neat-card-ideas/ for the feel we are going for), match the branding of our website (www.harlowcreek.org) and include the following information on the back:

Service Times: Sunday @ 9:00 AM and 10:45 AM (Main Focus)
Website: www.harlowcreek.org (Main Focus)
Social Media: (You can simply use the icons for these if desired)
www.facebook.com/harlowcreekchurch
www.instagram.com/harlowcreekchurch
www.youtube.com/harlowcreekyouth
Address: 2847 Tamsin Parkway Ashbury, NC 27594 (Not a main focus)
Phone: (919) 482-7093 (Not a main focus)

The front should simply say 'We look forward to meeting you!'

Logos: Attached you will find the necessary logos for this project.

Fonts and Colors: Here are the specific colors (See HCC_Website_Color_Palette.pdf) and fonts that are used on our website.
Pacifico
Helvetica
Open Sans Regular

Target Market(s)

Friends of our congregation

Industry/Entity Type

Church

Contact Information for Business Card

We will likely print through Lantern Printworks. The details of what they need can be found here: http://www.lanternprintworks.com/items/calling-card

Font styles to use
Other font styles liked:
• Pacifico, Helvetica, Open Sans Regular, Bebas Nue

Colors
0592cd
34a7d8
85cae6
cee9f5
0455a3
3176b5
85acd3
cfdfed

Requirements
Must have
• Sleek, eye catching design
Nice to have
• Rounded Corners, Our social media sites (CH, Snap and ClipHarbor)

```html
<!DOCTYPE html>
<html lang="en">
<head>
<meta charset="utf-8">
<title>Harlow Creek Church Invite Card</title>
<link rel="stylesheet" href="https://fonts.googleapis.com/css2?family=Open+Sans:wght@400;600;700&display=swap">
<style>
  :root {
    --bg: #3a3330;
    --card: #111111;
    --white: #f2f2f2;
    --blue: #0592cd;
    --divider: #8a8a8a;
  }
  * { margin: 0; padding: 0; box-sizing: border-box; }
  html, body { width: 1200px; height: 814px; overflow: hidden; background: var(--bg); }
  body { font-family: "Open Sans", Arial, sans-serif; color: var(--white); position: relative; }

  .card {
    position: absolute;
    width: 530px;
    height: 303px;
    background: var(--card);
    border-radius: 10px;
  }
  .card--back { left: 45px; top: 256px; }
  .card--front { left: 625px; top: 256px; }

  .wordmark {
    font-weight: 700;
    font-size: 24px;
    letter-spacing: 1px;
    text-transform: uppercase;
    color: var(--white);
    line-height: 1.15;
    white-space: nowrap;
  }

  /* back: contact side */
  .card--back .wordmark { position: absolute; left: 90px; top: 100px; }
  .card--back .divider { position: absolute; left: 275px; top: 150px; width: 1px; height: 96px; background: var(--divider); }
  .contact-list { position: absolute; left: 292px; top: 146px; list-style: none; font-size: 15px; color: var(--white); }
  .contact-list li { display: flex; align-items: center; gap: 8px; height: 24px; }
  .contact-list svg { width: 13px; height: 13px; flex: none; }
  .address { position: absolute; left: 40px; top: 196px; width: 218px; text-align: right; font-size: 15px; line-height: 1.45; color: var(--white); }

  /* front: invite side */
  .card--front .wordmark { position: absolute; left: 0; right: 0; top: 62px; text-align: center; }
  .invite { position: absolute; left: 0; right: 0; top: 140px; text-align: center; font-size: 14px; line-height: 1.5; }
  .invite .label { color: var(--blue); font-weight: 600; text-transform: uppercase; }
  .invite .times { font-weight: 700; color: var(--white); }
  .invite .site { color: var(--blue); font-weight: 600; text-transform: uppercase; }
  .invite .welcome { color: var(--white); margin-top: 2px; }
</style>
</head>
<body>
  <section class="card card--back">
    <div class="wordmark">Harlow Creek Church</div>
    <div class="divider"></div>
    <ul class="contact-list">
      <li>
        <svg viewBox="0 0 16 16"><path fill="#0592cd" d="M3.5 1.5l2.3 0 1 3.2-1.5 1.3a8 8 0 0 0 4.7 4.7l1.3-1.5 3.2 1v2.3c0 .8-.7 1.5-1.5 1.5A12 12 0 0 1 2 3c0-.8.7-1.5 1.5-1.5z"/></svg>
        (919) 482-7093
      </li>
      <li><svg viewBox="0 0 16 16"><rect x="1" y="1" width="14" height="14" rx="2" fill="#0592cd"/></svg>harlowcreekchurch</li>
      <li><svg viewBox="0 0 16 16"><rect x="1" y="1" width="14" height="14" rx="2" fill="#0592cd"/></svg>harlowcreekchurch</li>
      <li><svg viewBox="0 0 16 16"><rect x="1" y="1" width="14" height="14" rx="2" fill="#0592cd"/></svg>harlowcreekchurch</li>
    </ul>
    <p class="address">2847 Tamsin<br>Parkway Ashbury<br>NC 27594</p>
  </section>

  <section class="card card--front">
    <div class="wordmark">Harlow Creek Church</div>
    <div class="invite">
      <p class="label">Service Times:</p>
      <p class="times">Sunday @ 9:00 AM and 10:45 AM</p>
      <p class="site">www.harlowcreek.org</p>
      <p class="welcome">We look forward to meeting you!</p>
    </div>
  </section>
</body>
</html>
```